Property Services Company Needs a Brochure Design

Looking for a new brochure design for an existing property services company.

We provide a range of property services from, market research, real estate brokerage, valuation and appraisal, property development and other real estate consulting services.

We would like a fresh modern brochure design with good graphics and features. Our colours are white, blue and orange.

The design should communicate, attention to detail, superior service delivery and distinction in results.
Updates

I would like the brochure to be roughly about 20 pages.

Containing the following,

1) An introduction
2) Contents Page
2) What we do
3) Our Services
4) Agency & Brokerage
5) Real Estate Consulting
6) Market Research
7) Appraisal & Valuation
8) Project Management
9) Property Development

I would also like icons to represent items 4,5,6,7,8 & 9, they should be represented vertically on each of the pages from the contents page and highlighted individually on the pages that they represent.. i.e. on appraisal & valuation page, all six icons will be arranged vertically and the appraisal and valuations icon will be highlighted.

I will also like to have images that depict the services on the various pages.

I have some pages I think will flow which I will upload shortly.

Industry/Entity Type

Real Estate

Font styles to use
Serif

Colors
f78f20
0455a3

```html
<!DOCTYPE html>
<html lang="en">
<head>
<meta charset="utf-8">
<title>Halvercourt – Services Brochure Spread</title>
<link rel="stylesheet" href="https://fonts.googleapis.com/css2?family=Tinos:wght@400;700&display=swap">
<style>
  :root {
    --navy: #2b2360;
    --orange: #e05a12;
    --ink: #1d1d1d;
    --paper: #ffffff;
    --frame: #9a9a9a;
    --fold: #8a8a8a;
  }
  * { margin: 0; padding: 0; box-sizing: border-box; }
  html, body { width: 1200px; height: 864px; overflow: hidden; background: var(--paper); }
  body { position: relative; font-family: "Tinos", "Times New Roman", serif; color: var(--ink); }

  .spread {
    position: absolute; left: 40px; top: 35px; width: 1120px; height: 793px;
    border: 1px solid var(--frame); background: var(--paper); overflow: hidden;
  }
  .spread > * { position: absolute; }

  .photo { display: block; }
  .photo--architect { left: 0; top: 0; width: 355px; height: 280px;
    background: linear-gradient(160deg, #e9e8e4 0%, #c9c6bf 45%, #6d6a66 100%); }
  .photo--site-team { left: 785px; top: 0; width: 335px; height: 233px;
    background: linear-gradient(200deg, #9cc3e6 0%, #d8c24a 45%, #7a8d55 75%, #3d3b39 100%); }
  .photo--reader { left: 65px; top: 540px; width: 415px; height: 253px;
    background: linear-gradient(180deg, #f3f1ee 0%, #cfc9c0 40%, #3a3f5a 100%);
    clip-path: polygon(150px 0, 320px 0, 320px 90px, 100% 90px, 100% 100%, 0 100%, 0 90px, 150px 90px); }

  .skyline { background: linear-gradient(180deg, #f1f1f1, #dcdcdc); }
  .skyline--left { left: 412px; top: 40px; width: 76px; height: 153px; }
  .skyline--right { left: 622px; top: 23px; width: 103px; height: 207px; }

  .services-title {
    left: 365px; top: 188px; width: 160px; text-align: center;
    font-weight: 700; font-size: 33px; letter-spacing: 0.5px; color: var(--navy);
  }

  .rule { left: 0; width: 1120px; }
  .rule--orange { top: 231px; height: 7px; background: var(--orange); }
  .rule--navy { top: 757px; height: 6px; background: var(--navy); }

  .fold { left: 559px; top: 0; width: 1px; height: 793px; background: var(--fold); }

  .service-panel {
    top: 281px; height: 368px; padding: 16px 5px 0 12px; color: #fff;
    font-size: 12.4px; line-height: 14.6px;
  }
  .service-panel--navy { background: var(--navy); }
  .service-panel--orange { background: var(--orange); }
  .service-panel h2 { font-weight: 400; font-size: 15px; margin-bottom: 4px; }
  .panel--agency { left: 40px; width: 163px; }
  .panel--consulting { left: 215px; width: 163px; padding-left: 11px; }
  .panel--research { left: 390px; width: 170px; padding-left: 11px; }

  .page-text { font-size: 12.4px; line-height: 14.6px; }
  .page-text h2 { font-weight: 700; font-size: 15px; line-height: 17px; }
  .page-text p + p { margin-top: 4px; }
  .heading--navy { color: var(--navy); }
  .heading--orange { color: var(--orange); font-weight: 700; }
  .col--projects { left: 600px; top: 256px; width: 157px; }
  .col--projects .heading--orange { margin-top: 6px; }
  .col--about { left: 787px; top: 256px; width: 290px; }
  .col--about h2 { font-weight: 400; letter-spacing: 0.3px; margin-bottom: 5px; }
</style>
</head>
<body>
  <main class="spread">
    <div class="photo photo--architect" role="img" aria-label="Photo: smiling businessman in a hard hat reviewing building plans"></div>
    <div class="skyline skyline--left" role="img" aria-label="Pale building skyline graphic"></div>
    <h1 class="services-title">SERVICES</h1>
    <div class="skyline skyline--right" role="img" aria-label="Pale building skyline graphic"></div>
    <div class="photo photo--site-team" role="img" aria-label="Photo: construction team in hard hats discussing plans on site"></div>

    <div class="rule rule--orange"></div>

    <section class="service-panel service-panel--navy panel--agency">
      <h2>Agency&amp; Brokerage</h2>
      <p>The brokerage team, covers both landlords and tenants across the residential and commercial markets. With a large database of industry specific individuals and corporate twinned with a large database of inventory, we are able to very quickly understand the needs of our clients and find the perfect fit. We enjoy long standing relationships with many of our clients and landlords, and are always happy to meet with new clients to advise on how best to maximize their rental return or budget.</p>
    </section>

    <section class="service-panel service-panel--orange panel--consulting">
      <h2>Consulting</h2>
      <p>We provide a broad range of consulting services, we understand that out client needs may vary and our experienced team are at hand to provide tailored solutions to their needs. Our professional services include corporate planning, feasibility studies, market studies, due diligence, property tax, litigation, asset review and framework for foreign direct investment.</p>
    </section>

    <section class="service-panel service-panel--navy panel--research">
      <h2>Market Research</h2>
      <p>Our market research team, regularly conduct surveys across a wide range of areas in both the commercial and residential markets. They regularly produce market reports that can be used for a wide range of purposes. This information also provides our team members with superior knowledge of market trends, price shifts, occupancy rates and other unique trends. The information provided allows us to provide information useful for forecasting growth and trends in the market.</p>
    </section>

    <div class="photo photo--reader" role="img" aria-label="Photo: smiling businessman in a suit reading a newspaper on a sofa"></div>

    <div class="fold"></div>

    <section class="page-text col--projects">
      <h2 class="heading--navy">Project Management&amp; Property Development</h2>
      <p>Our project management team, with vast experience across commercial and residential developments provide the much needed support to achieve your dream property or office, allowing our clients to concentrate on their core business. We provide accurate information from financing, to design concept to budgeting and construction management. We take pride in creating inspirational&nbsp; developments that people can live, work and enjoy, whilst adding value.</p>
      <h2 class="heading--orange">Valuation &amp; Appraisal</h2>
      <p>We provide valuation and appraisal services to clients across a broad spectrum. Our valuation advice can provide information to assist with portfolio valuation, single asset valuation, financial reporting valuation. These services are provided to individuals, financial institutions and corporates. Appraisal methods will vary based on the specific needs of our clients</p>
    </section>

    <section class="page-text col--about">
      <h2 class="heading--orange">WHAT WE DO</h2>
      <p>Halvercourt is a leading property services company, incorporated in 1984, providing bespoke solutions in advisory, brokerage and turnkey solutions to owners, occupiers and property investors. Over the years we have expanded our services with a foundation based on core strengths, unrivalled local expertise, network and knowledge combined with strategic partnership. As well as providing property solutions we also develop commercial and residential units.</p>
      <p>Our growth has been based on maintaining relationships with our extensive client base, ranging from financial institutions, government agencies, airlines and servicing companies, manufacturing companies, multinationals and local</p>
      <p>corporations, to private developers and investors. Our clients depend on our ability to draw on years of experience in the local market, our professionals know their communities and the property market inside and out, and provide knowledgeable, creative solutions to all their real estate needs.</p>
      <p>The combination of our integrated services allows us to provide a superior end to end solution to our clients, customized to their own requirements.&nbsp; Market research is a core component to our business model, allowing us to make informed decisions based based on research findings.&nbsp; Our brokerage team also benefits from this information, allowing our associates to advise clients on how best to maximise return on their investment on the sale or buy side within a short timeline.</p>
      <p>We pay great attention to detail in consideration of our client requirements, delivering mandates with distinction.</p>
    </section>

    <div class="rule rule--navy"></div>
  </main>
</body>
</html>
```